QVR business card

Need a business card for a company that provides instructional design and elearning development services. The website is here: http://quorvane.studio/

I'm attaching a current logo, as well as the old business card design. While I like to keep it clean, the old design is too simplistic for my liking. The only idea I want to reuse from the old design is placing industry jargon on the back of the card, just need a better way to present it. But if you have other ideas for the back--feel free to experiment.

Please use the colors complementary to the color we have on the website. Thank you!

```html
<!DOCTYPE html>
<html lang="en">
<head>
<meta charset="utf-8">
<title>QVR business card</title>
<link rel="stylesheet" href="https://fonts.googleapis.com/css2?family=Open+Sans:wght@400;600&display=swap">
<style>
  :root {
    --stage: #9a9a9a;
    --stage-light: #c9c9c9;
    --teal: #35b3ad;
    --teal-deep: #15918a;
    --teal-faint: #a3cfcd;
    --sand: #d9cc9a;
    --ink: #444444;
    --paper: #ffffff;
    --paper-shade: #e4e4e4;
    --white: #ffffff;
  }
  * { box-sizing: border-box; margin: 0; padding: 0; }
  html, body {
    width: 1200px; height: 900px; overflow: hidden;
  }
  body {
    position: relative;
    background: radial-gradient(ellipse at 40% 40%, var(--stage-light), var(--stage));
    font-family: "Open Sans", Arial, sans-serif;
  }
  .card {
    position: absolute;
    width: 560px; height: 320px;
    overflow: hidden;
    box-shadow: 0 10px 24px rgba(0,0,0,0.35);
  }

  /* Front */
  .card-front {
    left: 170px; top: 90px; z-index: 2;
    background: linear-gradient(100deg, var(--paper) 35%, var(--paper-shade));
  }
  .card-front .wave { position: absolute; left: 0; bottom: 0; width: 560px; height: 90px; }
  .brand-mark {
    position: absolute; display: flex; align-items: center; gap: 12px;
  }
  .brand-mark .dot { width: 26px; height: 26px; border-radius: 50%; }
  .brand-name { font-weight: 600; letter-spacing: 2px; }
  .card-front .brand-mark { left: 36px; top: 36px; }
  .card-front .dot { background: var(--teal); }
  .card-front .brand-name { font-size: 48px; color: var(--teal); }
  .deco-disc {
    position: absolute; right: -40px; top: 70px;
    width: 220px; height: 220px; border-radius: 50%;
    background: var(--teal-faint); opacity: 0.55;
  }
  .holder-name {
    position: absolute; left: 178px; top: 140px;
    font-size: 22px; color: var(--ink); letter-spacing: 0.5px;
  }
  .contact-list { position: absolute; left: 182px; top: 182px; list-style: none; }
  .contact-list li {
    display: flex; align-items: center; gap: 8px;
    font-size: 14px; color: var(--ink); margin-bottom: 8px;
  }
  .contact-list svg { width: 14px; height: 14px; fill: var(--teal); flex: none; }

  /* Back */
  .card-back {
    left: 470px; top: 470px; z-index: 1;
    background: linear-gradient(100deg, var(--teal) 20%, var(--teal-deep));
    color: var(--white);
  }
  .card-back .brand-mark { left: 50%; transform: translateX(-50%); top: 28px; }
  .card-back .dot { background: var(--white); }
  .card-back .brand-name { font-size: 44px; color: var(--white); }
  .help-heading {
    position: absolute; left: 0; right: 0; top: 112px;
    display: flex; align-items: center; gap: 14px; padding: 0 0;
  }
  .help-heading .rule { flex: 1; height: 2px; background: var(--sand); }
  .help-heading h2 {
    font-size: 18px; font-weight: 600; color: var(--sand); letter-spacing: 1px; white-space: nowrap;
  }
  .jargon {
    position: absolute; list-style: none;
    font-size: 14px; line-height: 24px; letter-spacing: 1px; text-transform: uppercase;
  }
  .jargon li { word-spacing: 12px; }
  .jargon-left { left: 24px; top: 160px; }
  .jargon-right { right: 24px; top: 210px; text-align: right; }
</style>
</head>
<body>

<section class="card card-front" aria-label="Business card front">
  <svg class="wave" viewBox="0 0 560 90" preserveAspectRatio="none" aria-hidden="true">
    <path d="M0 52 C150 22 330 22 560 40 L560 90 L0 90 Z" fill="var(--sand)"/>
    <path d="M0 66 C170 30 360 30 560 14 L560 90 L0 90 Z" fill="var(--teal)"/>
  </svg>
  <div class="deco-disc" aria-hidden="true"></div>
  <div class="brand-mark">
    <span class="dot" aria-hidden="true"></span>
    <span class="brand-name">QVR</span>
  </div>
  <p class="holder-name">Marek Dovlanski</p>
  <ul class="contact-list">
    <li>
      <svg viewBox="0 0 24 24" aria-hidden="true"><path d="M6.6 10.8a15 15 0 0 0 6.6 6.6l2.2-2.2a1 1 0 0 1 1-.25 11.4 11.4 0 0 0 3.6.57 1 1 0 0 1 1 1V20a1 1 0 0 1-1 1A17 17 0 0 1 3 4a1 1 0 0 1 1-1h3.5a1 1 0 0 1 1 1c0 1.25.2 2.45.57 3.6a1 1 0 0 1-.25 1z"/></svg>
      555-014-2287
    </li>
    <li>
      <svg viewBox="0 0 24 24" aria-hidden="true"><path d="M2 5h20v14H2z M2 5l10 8 10-8" stroke="var(--paper)" stroke-width="1.5"/></svg>
      mdovlanski@quorvane.studio
    </li>
    <li>
      <svg viewBox="0 0 24 24" aria-hidden="true"><circle cx="12" cy="12" r="10"/><path d="M2 12h20M12 2c3 3 3 17 0 20M12 2c-3 3-3 17 0 20" stroke="var(--paper)" stroke-width="1.3" fill="none"/></svg>
      www.Quorvane.Studio
    </li>
  </ul>
</section>

<section class="card card-back" aria-label="Business card back">
  <div class="brand-mark">
    <span class="dot" aria-hidden="true"></span>
    <span class="brand-name">QVR</span>
  </div>
  <div class="help-heading">
    <span class="rule"></span>
    <h2>HOW CAN WE HELP?</h2>
    <span class="rule"></span>
  </div>
  <ul class="jargon jargon-left">
    <li>Mobile Learning SCORM</li>
    <li>Instructional Design LMS</li>
    <li>MOOCs eLearning HTML5</li>
  </ul>
  <ul class="jargon jargon-right">
    <li>Adult Learning Theory</li>
    <li>Gamification Classroom</li>
    <li>xAPI Blended Learning</li>
  </ul>
</section>

</body>
</html>
```